Finding the Root: Reason in Clinical Choice-Crafting

I'd like a cover that looks like it would fit on the shelf next to "The Illness Mirage" by Corwin Talley, "The Close of Forgetting" by Hugh Marchetti, "Meal Mend" by Paul Grieve, "The Energy Restart Plan" by Oscar Pemberley or "The Gland Restart Plan" by the same or "The Cortex Restart Plan" by the same ... either text only (with some interesting fonts that make the title stand out, and the subtitle smaller) or a relevant image, though I'm not entirely sure what that would be since this is a book about big-picture medical decision making.
Author name is Dr Tessa Morrow, NMD
I'll eventually request an e-book, paperback, and audio cover from the winner...

Target Market(s)

practicing physicians

Industry/Entity Type

medicine

Requirements
Must have
• look similar to other books in the genre

```html
<!DOCTYPE html>
<html lang="en">
<head>
<meta charset="utf-8">
<title>Finding the Root – Book Cover</title>
<link href="https://fonts.googleapis.com/css2?family=Oswald:wght@400;700&family=Montserrat:wght@400&display=swap" rel="stylesheet">
<style>
  :root {
    --backdrop: #03070a;
    --paper: #f9f9f7;
    --ink: #0a0a0a;
    --sage: #68844a;
    --emblem-tone: #d4d6cc;
    --subtitle-ink: #1d1d1d;
  }
  html, body {
    margin: 0;
    padding: 0;
    width: 1200px;
    height: 1200px;
    overflow: hidden;
    background: var(--backdrop);
  }
  .cover-canvas { display: block; width: 1200px; height: 1200px; }
  .cover-sheet { fill: var(--paper); }
  .title-light {
    font-family: "Oswald", "Arial Narrow", sans-serif;
    font-weight: 400;
    fill: var(--ink);
  }
  .title-heavy {
    font-family: "Oswald", "Arial Narrow", sans-serif;
    font-weight: 700;
    fill: var(--sage);
  }
  .subtitle {
    font-family: "Montserrat", Arial, sans-serif;
    font-weight: 400;
    fill: var(--subtitle-ink);
  }
  .subtitle-rule { stroke: var(--sage); stroke-width: 1.2; }
  .emblem { fill: var(--emblem-tone); }
  .author {
    font-family: "Oswald", "Arial Narrow", sans-serif;
    font-weight: 700;
    fill: var(--sage);
  }
</style>
</head>
<body>
<svg class="cover-canvas" viewBox="0 0 1200 1200" xmlns="http://www.w3.org/2000/svg">
  <rect class="cover-sheet" x="273" y="109" width="655" height="979"/>

  <text class="title-light" x="598" y="306" font-size="166" text-anchor="middle" textLength="524" lengthAdjust="spacingAndGlyphs">FINDING</text>
  <text class="title-light" x="598" y="474" font-size="166" text-anchor="middle" textLength="156" lengthAdjust="spacingAndGlyphs">THE</text>
  <text class="title-heavy" x="599" y="753" font-size="310" text-anchor="middle" textLength="531" lengthAdjust="spacingAndGlyphs">ROOT</text>

  <circle class="emblem" cx="409" cy="870" r="70" role="img" aria-label="Circular maze emblem with a medical cross at its centre"/>

  <line class="subtitle-rule" x1="487" y1="815" x2="869" y2="815"/>
  <text class="subtitle" x="507" y="864" font-size="35" textLength="360" lengthAdjust="spacingAndGlyphs">REASON IN CLINICAL</text>
  <text class="subtitle" x="507" y="903" font-size="35" textLength="360" lengthAdjust="spacingAndGlyphs">CHOICE-CRAFTING</text>
  <line class="subtitle-rule" x1="487" y1="926" x2="869" y2="926"/>

  <text class="author" x="599" y="1032" font-size="38" text-anchor="middle" textLength="426" lengthAdjust="spacing">DR TESSA MORROW, NMD</text>
</svg>
</body>
</html>
```